Foot doctor needs feet friendly business cards.

Business cards for Podiatrist. Needs to look professional and modern. Back side put an appointment card, and try to put a little basic street map somewhere on card along with all of our contact info below:

Marcus Dovan, DPM, Inc.
Diplomate, National Council of Lower Limb Medicine
Call: 1.877.Toes.482
1.555.283.9146
Fax: 1.555.671.3820
Email: info@DrDovanclinic.example
Web: www.DrDovanclinic.example
2847 W. Harbor Ln. Suite 204
Costa Mesa, CA 90000

```html
<!DOCTYPE html>
<html lang="en">
<head>
<meta charset="UTF-8">
<title>Appointment Card</title>
<link rel="stylesheet" href="https://fonts.googleapis.com/css2?family=Source+Sans+3:wght@600;700&display=swap">
<style>
  :root {
    --ink: #1c1f24;
    --band-light: #3fb9ea;
    --band-dark: #1a72bf;
    --band-text: #14263a;
    --paper: #ffffff;
    --tint-soft: rgba(160, 180, 225, 0.28);
    --tint-faint: rgba(200, 212, 240, 0.15);
  }
  html, body {
    margin: 0;
    padding: 0;
    width: 1200px;
    height: 763px;
    overflow: hidden;
    background: var(--paper);
  }
  .card {
    position: relative;
    width: 1200px;
    height: 763px;
    background: var(--paper);
    font-family: "Source Sans 3", "Myriad Pro", sans-serif;
    color: var(--ink);
    overflow: hidden;
  }
  .card__backdrop {
    position: absolute;
    inset: 0;
    background:
      radial-gradient(ellipse 55% 60% at 72% 68%, var(--tint-soft), transparent 70%),
      radial-gradient(ellipse 40% 45% at 12% 30%, var(--tint-faint), transparent 70%),
      radial-gradient(ellipse 50% 30% at 50% 95%, var(--tint-soft), transparent 75%);
  }
  .card__title {
    position: absolute;
    top: 38px;
    left: 0;
    width: 100%;
    margin: 0;
    text-align: center;
    font-weight: 700;
    font-size: 58px;
    letter-spacing: -0.5px;
  }
  .field {
    position: absolute;
    margin: 0;
    font-weight: 700;
    font-size: 37px;
    letter-spacing: -1px;
  }
  .field--for { left: 142px; top: 164px; }
  .field--date { left: 142px; top: 288px; }
  .field--time { left: 620px; top: 288px; }
  .field--location { left: 144px; top: 430px; }
  .notice-band {
    position: absolute;
    left: 0;
    top: 602px;
    width: 1200px;
    height: 120px;
  }
  .notice-band svg { position: absolute; inset: 0; }
  .notice-band__message {
    position: absolute;
    left: 20px;
    top: 26px;
    width: 650px;
    margin: 0;
    text-align: center;
    font-weight: 600;
    font-size: 25px;
    line-height: 1.2;
    letter-spacing: -0.6px;
    color: var(--band-text);
  }
  .notice-band__call {
    position: absolute;
    left: 746px;
    top: 34px;
    margin: 0;
    font-weight: 600;
    font-size: 44px;
    letter-spacing: -0.5px;
    color: var(--paper);
  }
</style>
</head>
<body>
<main class="card">
  <div class="card__backdrop" role="img" aria-label="Soft pale blue geometric background pattern"></div>

  <h1 class="card__title">APPOINTMENT</h1>

  <p class="field field--for">FOR :</p>
  <p class="field field--date">DATE :</p>
  <p class="field field--time">TIME :</p>
  <p class="field field--location">LOCATION :</p>

  <section class="notice-band">
    <svg width="1200" height="120" viewBox="0 0 1200 120">
      <rect x="0" y="0" width="1200" height="120" fill="var(--band-light)"/>
      <polygon points="648,0 1200,0 1200,120 770,120" fill="var(--band-dark)"/>
      <polygon points="636,0 648,0 770,120 758,120" fill="var(--paper)"/>
    </svg>
    <p class="notice-band__message">IF YOU ARE UNABLE TO KEEP UP THE APPOINTMENT<br>PLEASE CONTACT US AS SOON AS POSSIBLE.</p>
    <p class="notice-band__call">CALL : 1 877 863 7482</p>
  </section>
</main>
</body>
</html>
```